We need a business card for our gym. We are a PowerCore affiliate in Decatur Georgie established 2008. Our company name is Rally Functional Fitness. PowerCore Building Prime Fitness. Instagram and website is @rallygym. Hashtags we use #rallywithheart #madetorally We want something similar to the the black and neon green design attached but a different color scheme. No neon colors. Are company colors are the same as the blue and white card attached. We are open to ideas as far as colors however - just no neon.

Contact Information for Business Card

Rally Functional Fitness
472 Halvern Drive
Decatur GA 30041
Phone 404.555.0187 Website www.rallygym.example

Font styles to use
Other font styles liked:
• Futura Extra Bold Condensed

Colors

Designer to choose colors to be used in the design.

Requirements
Must have
• Our primary font we typically use for our name is Futura Extra Bold Condensed
Nice to have
• I attached a card from that is black and neon green from Zorva that we would like something similar. The blue and white is more similar to our colors. We also use have used black and white in the past. We use the chevrons as out logo. We are a PowerCore affiliate so I included a logo from them as well that may or may not be used on the card. Our instagram is @rallygym hashtags #madetorally #rallywithheart
Should not have
• No neon colors

```html
<!DOCTYPE html>
<html lang="en">
<head>
<meta charset="utf-8">
<title>Rally Functional Fitness — Business Card</title>
<link href="https://fonts.googleapis.com/css2?family=Anton&family=Montserrat:wght@400;500&display=swap" rel="stylesheet">
<style>
  :root {
    --stage: #2b2b2b;
    --card: #222222;
    --card-edge: #1a1a1a;
    --accent: #86cdef;
    --mark: #bfbfbf;
  }
  * { margin: 0; padding: 0; box-sizing: border-box; }
  html, body {
    width: 1200px; height: 901px; overflow: hidden;
    background: var(--stage);
  }
  .stage {
    position: relative; width: 1200px; height: 901px;
  }
  .card {
    position: absolute; left: 260px; width: 680px; height: 389px;
    background: var(--card);
    border: 1px solid var(--card-edge);
    box-shadow: 0 10px 28px rgba(0,0,0,.45);
  }
  .card--back { top: 42px; }
  .card--front { top: 470px; }

  /* back: brand mark */
  .brand-mark {
    position: absolute; inset: 0;
    display: flex; align-items: center; justify-content: center; gap: 18px;
    font-family: "Anton", "Oswald", sans-serif;
    font-size: 96px; letter-spacing: 4px; color: var(--mark);
  }
  .brand-mark__square {
    width: 34px; height: 34px; background: var(--mark);
  }

  /* front */
  .wordmark {
    position: absolute; left: 52px; top: 128px; width: 250px;
    font-family: "Anton", "Oswald", sans-serif; color: var(--accent);
    text-transform: uppercase; text-align: center; line-height: 1;
  }
  .wordmark__name { font-size: 84px; letter-spacing: 2px; }
  .wordmark__tag { font-size: 27px; letter-spacing: .5px; margin-top: 6px; }

  .divider {
    position: absolute; left: 340px; top: 88px; width: 2px; height: 212px;
    background: var(--accent); opacity: .8;
  }
  .contact {
    position: absolute; left: 372px; top: 92px;
    color: var(--accent);
    font-family: "Montserrat", sans-serif; font-size: 19px; line-height: 1.25;
  }
  .contact__name {
    font-family: "Anton", "Oswald", sans-serif;
    font-size: 29px; letter-spacing: 1.5px; text-transform: uppercase;
    word-spacing: 10px;
  }
  .contact__role { text-transform: uppercase; letter-spacing: 1px; margin-bottom: 14px; }
  .contact__address { margin-bottom: 14px; }
  .contact__line { display: flex; align-items: center; gap: 10px; }
  .contact__line svg { width: 16px; height: 16px; flex: none; }
</style>
</head>
<body>
<div class="stage">
  <section class="card card--back" aria-label="Card back">
    <div class="brand-mark">
      <span class="brand-mark__square"></span>
      <span>RALLY</span>
    </div>
  </section>

  <section class="card card--front" aria-label="Card front">
    <div class="wordmark">
      <div class="wordmark__name">Rally</div>
      <div class="wordmark__tag">Functional Fitness</div>
    </div>
    <div class="divider"></div>
    <div class="contact">
      <div class="contact__name">Marcus Delaney</div>
      <div class="contact__role">Expert Coaches</div>
      <div class="contact__address">472 Halvern Drive<br>Decatur GA 30041</div>
      <div class="contact__line">
        <svg viewBox="0 0 24 24" aria-hidden="true"><path fill="currentColor" d="M6.6 10.8a15.1 15.1 0 0 0 6.6 6.6l2.2-2.2a1 1 0 0 1 1-.25 11.4 11.4 0 0 0 3.6.57 1 1 0 0 1 1 1V20a1 1 0 0 1-1 1A17 17 0 0 1 3 4a1 1 0 0 1 1-1h3.5a1 1 0 0 1 1 1c0 1.25.2 2.45.57 3.57a1 1 0 0 1-.25 1z"/></svg>
        <span>404.555.0187</span>
      </div>
      <div class="contact__line">
        <svg viewBox="0 0 24 24" aria-hidden="true"><circle cx="12" cy="12" r="9" fill="none" stroke="currentColor" stroke-width="2.4"/><path d="M3 12h18M12 3c3 3 3 15 0 18M12 3c-3 3-3 15 0 18" fill="none" stroke="currentColor" stroke-width="1.8"/></svg>
        <span>www.rallygym.example</span>
      </div>
    </div>
  </section>
</div>
</body>
</html>
```